International oil and gas consultancy business needs a web design

Hello, I need a web design for a new oil and gas auditing consultancy business. My business undertakes contract audit assignments to review past costs of oil and gas operations (see attached Excel file for more details of the businesses services). I need the design to give the impression of a professional consultancy style of business, rather than a retail style of website. Note: this job is for LAYOUT DESIGN ONLY and not coding / development work.
The following are my key design principles:
1. BASIC DESIGN: I am after a simple and static web design. I don't want the pages busy or cluttered with too many images or detail.
2. HORIZONTAL TABS: I require a horizontal set of tabs towards the top of the screens (see Excel file) which remain in the same position on every page.
3. META TAG PLANNING: The design should allow for effective positioning of content so that key meta tag words can easily be built during the technical build stage.
4. NUMBER OF PAGES: The site will eventually have a maximum of 10 pages. Seven of the pages will reside under the tabs. Can you please present your opening submission for the first two page.
5. USE OF MY LOGO: The attached logo (JPEG file) should be used throughout the website. Please don't change the shape and colour.
6. COLOUR SCHEMES: Can you please consider any of the 3 colour schemes below:
A - dark red (to match the logo), light grey and perhaps another of your liking;
B - dark red (to match the logo), light cream and perhaps another of your liking;
C - dark red (to match the logo), white and perhaps another of your liking.
7. WORD CONTENT: I have attached an Excel file which shows the estimated word content for each page.
8. FUTURE USE OF DESIGN: I'm planning on building a Wordpress website. Can you please ensure the layout design supports this application.

Target Market(s)

oil and gas companies (small and large)

Industry/Entity Type

Oil And Gas

Font styles to use
Sans Serif

Requirements
Nice to have
• The KRL logo and business name should ideally be next to each other. Also, the logo and name should be part of the background graphics, not above it.

```html
<!DOCTYPE html>
<html lang="en">
<head>
<meta charset="utf-8">
<title>Kestrel Resource Ledger</title>
<link href="https://fonts.googleapis.com/css2?family=Roboto:wght@300;400;500;700&display=swap" rel="stylesheet">
<style>
  :root {
    --brand-red: #8c1a1f;
    --brand-red-dark: #6e1216;
    --ink: #3a3a3a;
    --light-grey: #eef0f3;
    --nav-grey: #e4e4e4;
    --footer: #333333;
    --white: #ffffff;
  }
  * { margin: 0; padding: 0; box-sizing: border-box; }
  html, body { width: 973px; height: 1200px; overflow: hidden; }
  body {
    position: relative;
    font-family: "Roboto", Arial, sans-serif;
    background: var(--white);
    color: var(--ink);
  }
  .site-header { position: absolute; left: 0; top: 0; width: 973px; height: 113px; }
  .brand { position: absolute; left: 85px; top: 26px; text-align: left; }
  .brand-name {
    display: flex; align-items: center; gap: 8px;
    font-size: 38px; font-weight: 700; color: var(--brand-red); line-height: 1;
    letter-spacing: 2px;
  }
  .brand-mark { width: 14px; height: 14px; background: var(--brand-red); }
  .brand-tagline { font-size: 12px; color: var(--ink); margin-top: 6px; }
  .main-nav {
    position: absolute; left: 284px; top: 36px; height: 41px; display: flex;
    border-radius: 5px; overflow: hidden;
    box-shadow: 0 1px 2px rgba(0,0,0,.2);
  }
  .main-nav a {
    display: flex; align-items: center; justify-content: center;
    height: 41px; font-size: 12px; color: var(--white); text-decoration: none;
    background: linear-gradient(#94212a, #7c151b);
    border-left: 1px solid #5e0f13;
  }
  .main-nav a.is-active {
    background: linear-gradient(#f2f2f2, var(--nav-grey));
    color: #555; border-left: none;
  }
  .hero {
    position: absolute; left: 0; top: 113px; width: 973px; height: 439px;
    background: linear-gradient(180deg, #6d6f86 0%, #a0607a 18%, #e3583a 42%, #f7751c 62%, #e84f14 78%, #3b3536 92%, #2e2d30 100%);
  }
  .hero-caption {
    position: absolute; left: 80px; top: 147px; width: 406px; height: 92px;
    background: rgba(90,90,90,.72); color: var(--white); padding: 14px 16px;
  }
  .hero-caption h1 { font-weight: 400; font-size: 31px; line-height: 1.05; }
  .hero-caption p { font-size: 16px; margin-top: 6px; padding-left: 4px; }
  .slider-dots { position: absolute; left: 931px; top: 27px; }
  .slider-dots span {
    display: block; width: 9px; height: 9px; border-radius: 50%;
    background: var(--white); margin-bottom: 6px;
  }
  .slider-dots span.is-current { background: var(--brand-red); }
  .welcome {
    position: absolute; left: 0; top: 560px; width: 973px; height: 161px;
    background: linear-gradient(#f7f8fa, #e9ebee); text-align: center;
  }
  .welcome h2 { margin-top: 38px; font-size: 18px; font-weight: 400; color: var(--brand-red); }
  .welcome p { width: 800px; margin: 14px auto 0; font-size: 12px; line-height: 24px; }
  .services-title {
    position: absolute; left: 0; top: 745px; width: 973px; text-align: center;
    font-size: 18px; font-weight: 400; color: var(--brand-red);
  }
  .service {
    position: absolute; top: 802px; width: 260px; text-align: center;
  }
  .service-icon { width: 116px; height: 116px; display: block; margin: 0 auto; }
  .service h3 { font-size: 16px; font-weight: 400; color: var(--brand-red); margin-top: 14px; }
  .service p { font-size: 10.5px; line-height: 18px; margin-top: 6px; }
  .read-more {
    display: inline-block; margin-top: 12px; width: 89px; height: 31px; line-height: 31px;
    background: linear-gradient(#9a232a, #7a141a); color: var(--white);
    font-size: 12px; text-decoration: none; border-radius: 2px;
    box-shadow: 0 1px 2px rgba(0,0,0,.3);
  }
  .site-footer {
    position: absolute; left: 0; top: 1100px; width: 973px; height: 100px;
    background: var(--footer); color: var(--white); font-size: 11.5px;
  }
  .copyright { position: absolute; left: 84px; top: 47px; }
  .legal-links { position: absolute; right: 85px; top: 45px; }
  .legal-links a { color: var(--white); text-decoration: none; }
</style>
</head>
<body>
  <header class="site-header">
    <div class="brand">
      <div class="brand-name"><span class="brand-mark"></span>KRL</div>
      <div class="brand-tagline">Kestrel Resource Ledger</div>
    </div>
    <nav class="main-nav">
      <a class="is-active" style="width:62px">Home</a>
      <a style="width:80px">About Us</a>
      <a style="width:75px">Services</a>
      <a style="width:103px">Our Partners</a>
      <a style="width:82px">Approach</a>
      <a style="width:113px">Why Choose Us</a>
      <a style="width:92px">Contact Us</a>
    </nav>
  </header>

  <section class="hero" role="img" aria-label="Oil drilling rig silhouetted against an orange sunset sky">
    <div class="hero-caption">
      <h1>Kestrel Resource Ledger</h1>
      <p>Lorem Ipsum is simply dummy text of the printing</p>
    </div>
    <div class="slider-dots">
      <span class="is-current"></span><span></span><span></span><span></span><span></span>
    </div>
  </section>

  <section class="welcome">
    <h2>WELCOME TO KESTREL RESOURCE LEDGER</h2>
    <p>Kestrel Resource Ledger is a Perth (Australia) based firm specialising in providing quality audit services for the oil and gas industry. Our skills and knowledge of oil and gas, along with a deep understanding of business commercial needs, ensures the high quality of our services</p>
  </section>

  <h2 class="services-title">Kestrel Resource Ledger specialise in the following services:</h2>

  <article class="service" style="left:77px">
    <svg class="service-icon" viewBox="0 0 116 116">
      <path d="M68 6 A52 52 0 0 1 110 52" fill="none" stroke="#d9b3b5" stroke-width="4"/>
      <path d="M6 64 A52 52 0 0 0 52 110" fill="none" stroke="#d9b3b5" stroke-width="4"/>
      <circle cx="58" cy="58" r="48" fill="var(--brand-red)"/>
      <path d="M58 37 L81 47 L58 57 L35 47 Z" fill="#fff"/>
      <path d="M35 51 L56 60 L56 82 L35 72 Z" fill="#fff"/>
      <path d="M81 51 L60 60 L60 82 L81 72 Z" fill="#fff"/>
    </svg>
    <h3>Joint Venture audits</h3>
    <p>Lorem Ipsum is simply dummy text of the printing and typesetting industry. Lorem Ipsum has been the industry's standard dummy text</p>
    <a class="read-more">Read More</a>
  </article>

  <article class="service" style="left:356px">
    <svg class="service-icon" viewBox="0 0 116 116">
      <path d="M68 6 A52 52 0 0 1 110 52" fill="none" stroke="#d9b3b5" stroke-width="4"/>
      <path d="M6 64 A52 52 0 0 0 52 110" fill="none" stroke="#d9b3b5" stroke-width="4"/>
      <circle cx="58" cy="58" r="48" fill="var(--brand-red)"/>
      <path d="M34 76 L52 58 L60 66 L78 48" fill="none" stroke="#fff" stroke-width="6" stroke-linejoin="round"/>
      <path d="M68 40 L86 40 L86 58 Z" fill="#fff"/>
    </svg>
    <h3>Contract audits</h3>
    <p>Lorem Ipsum is simply dummy text of the printing and typesetting industry. Lorem Ipsum has been the industry's standard dummy text</p>
    <a class="read-more">Read More</a>
  </article>

  <article class="service" style="left:635px">
    <svg class="service-icon" viewBox="0 0 116 116">
      <path d="M68 6 A52 52 0 0 1 110 52" fill="none" stroke="#f3cdb8" stroke-width="4"/>
      <path d="M6 64 A52 52 0 0 0 52 110" fill="none" stroke="#f3cdb8" stroke-width="4"/>
      <circle cx="58" cy="58" r="48" fill="var(--brand-red)"/>
      <text x="58" y="52" text-anchor="middle" font-family="Roboto, sans-serif" font-size="24" font-weight="700" fill="#fff">$</text>
      <circle cx="44" cy="62" r="6" fill="#fff"/>
      <path d="M32 80 Q32 70 44 70 Q56 70 56 80 Z" fill="#fff"/>
      <circle cx="72" cy="62" r="6" fill="#fff"/>
      <path d="M60 80 Q60 70 72 70 Q84 70 84 80 Z" fill="#fff"/>
    </svg>
    <h3>Operations audits</h3>
    <p>Lorem Ipsum is simply dummy text of the printing and typesetting industry. Lorem Ipsum has been the industry's standard dummy text</p>
    <a class="read-more">Read More</a>
  </article>

  <footer class="site-footer">
    <div class="copyright">Copyright ©&nbsp; 2014 Kestrel Resource Ledger</div>
    <div class="legal-links"><a>Terms and Conditions</a>&nbsp; | &nbsp;<a>Privacy policy</a></div>
  </footer>
</body>
</html>
```